Harborlane Products Flyer

Harborlane Lending Group, Inc.
Licensed Mortgage Company
Serving the DMV since 1997
"You open the Harborlane, we'll carry the load"
We specialize in...
FHA Loans
* Credit Scores as low as 500
* 203K Renovation Loans
Conventional Loans
* As little as 1% Down
* Bank Statement for Self-Employed
Investor Loans
* DSCR, & Fix & Flip
* Commercial & New Construction
Other Programs
* HELOCS & Reverse Mortgages
Call today for a free consultation
(800) 914-6027
www.harborlanehomeloans.com
NMLS #731860

```html
<!DOCTYPE html>
<html lang="en">
<head>
<meta charset="utf-8">
<title>Harborlane Products Flyer</title>
<link rel="stylesheet" href="https://fonts.googleapis.com/css2?family=Barlow:wght@500;600;700&family=Libre+Baskerville:wght@700&display=swap">
<style>
  :root {
    --bg: #0d1e29;
    --panel: #062633;
    --blue-top: #2b5bd0;
    --blue-bottom: #08128a;
    --edge-blue: #1d3fb5;
    --gold: #e6b84c;
    --gold-deep: #c98f2c;
    --white: #ffffff;
    --photo-top: #7d8a78;
    --photo-bottom: #3f6b35;
  }
  * { margin: 0; padding: 0; box-sizing: border-box; }
  html, body { width: 927px; height: 1200px; overflow: hidden; background: var(--bg); }
  .flyer {
    position: relative; width: 927px; height: 1200px; overflow: hidden;
    background: radial-gradient(ellipse at 50% 40%, #132a36 0%, var(--bg) 70%);
    color: var(--white); font-family: "Barlow", sans-serif;
  }
  .brand {
    position: absolute; top: 92px; left: 0; width: 927px;
    display: flex; justify-content: center; align-items: center; gap: 12px;
  }
  .brand-dot { width: 18px; height: 18px; border-radius: 50%; background: var(--gold); }
  .brand-name {
    font-family: "Libre Baskerville", serif; font-weight: 700; font-size: 34px;
    color: var(--gold); letter-spacing: 1px; text-transform: uppercase;
  }
  .hero-pill {
    position: absolute; left: 70px; top: 238px; width: 787px; height: 194px;
    border-radius: 97px; border: 2px solid var(--gold-deep);
    background: linear-gradient(180deg, var(--blue-top), var(--blue-bottom));
  }
  .company-name {
    position: absolute; left: 72px; top: 28px;
    font-family: "Libre Baskerville", serif; font-weight: 700; font-size: 31px;
    line-height: 46px; color: var(--gold); text-transform: uppercase;
  }
  .credential {
    position: absolute; left: 440px; display: flex; align-items: center; gap: 29px;
  }
  .credential.licensed { top: 28px; }
  .credential.region { top: 111px; }
  .credential-icon {
    width: 56px; height: 56px; border-radius: 50%; background: var(--white);
    display: flex; align-items: center; justify-content: center; flex: none;
  }
  .credential-text {
    font-weight: 700; font-size: 19px; line-height: 29px; letter-spacing: 0.5px;
    text-transform: uppercase;
  }
  .tagline {
    position: absolute; top: 468px; left: 0; width: 927px; text-align: center;
    font-family: "Libre Baskerville", serif; font-weight: 700; font-size: 20px;
    text-transform: uppercase;
  }
  .section-rule {
    position: absolute; top: 520px; left: 69px; width: 789px;
    display: flex; align-items: center; gap: 16px;
  }
  .section-rule::before, .section-rule::after {
    content: ""; flex: 1; height: 1px; background: var(--white);
  }
  .section-rule span { font-weight: 700; font-size: 18px; text-transform: uppercase; }
  .product {
    position: absolute; width: 254px; text-align: center;
  }
  .product-title {
    height: 35px; border-radius: 18px; border: 1px solid var(--gold-deep);
    background: linear-gradient(180deg, var(--blue-top), var(--blue-bottom));
    font-weight: 700; font-size: 17px; line-height: 33px; text-transform: uppercase;
    letter-spacing: 0.3px;
  }
  .product-list { list-style: none; margin-top: 15px; }
  .product-list li {
    display: flex; justify-content: center; align-items: center; gap: 12px;
    font-size: 15px; line-height: 29px; white-space: nowrap; margin: 0 -60px;
  }
  .fha { left: 139px; top: 584px; }
  .investor { left: 535px; top: 584px; }
  .conventional { left: 139px; top: 726px; }
  .other { left: 535px; top: 726px; }
  .family-photo { position: absolute; left: 0; top: 870px; }
  .contact-card {
    position: absolute; width: 205px; height: 171px; border-radius: 18px;
    background: var(--panel); border: 1.5px solid var(--edge-blue);
    padding: 26px 17px 0;
  }
  .contact-card .icon {
    width: 36px; height: 36px; border-radius: 50%; background: var(--white);
    display: flex; align-items: center; justify-content: center; margin-bottom: 12px;
  }
  .contact-card p { font-size: 14px; line-height: 23px; font-weight: 500; }
  .contact-card .big { font-weight: 700; font-size: 22px; line-height: 32px; }
  .call { left: 67px; top: 939px; }
  .web { left: 654px; top: 871px; }
  .web p { font-size: 13px; }
</style>
</head>
<body>
<div class="flyer">
  <div class="brand">
    <span class="brand-dot"></span>
    <span class="brand-name">Harborlane</span>
  </div>

  <div class="hero-pill">
    <div class="company-name">Harborlane<br>Lending Group,<br>Inc.</div>
    <div class="credential licensed">
      <div class="credential-icon">
        <svg width="30" height="30" viewBox="0 0 30 30"><path d="M15 2l3.5 3 4.5-.5.5 4.5 3 3.5-3 3.5-.5 4.5-4.5-.5L15 28l-3.5-3-4.5.5-.5-4.5-3-3.5 3-3.5.5-4.5 4.5.5z" fill="#0d1a8f"/><path d="M10 15l3.5 3.5L20 12" stroke="#fff" stroke-width="2.5" fill="none" stroke-linecap="round" stroke-linejoin="round"/></svg>
      </div>
      <div class="credential-text">Licensed Mortgage<br>Company</div>
    </div>
    <div class="credential region">
      <div class="credential-icon">
        <svg width="30" height="30" viewBox="0 0 30 30" fill="#0d1a8f"><rect x="11" y="2" width="8" height="7" rx="1"/><rect x="2" y="20" width="7" height="7" rx="1"/><rect x="11.5" y="20" width="7" height="7" rx="1"/><rect x="21" y="20" width="7" height="7" rx="1"/><path d="M14 9h2v5h9v6h-2v-4h-7v4h-2v-4H7v4H5v-6h9z"/></svg>
      </div>
      <div class="credential-text">Serving the DMV<br>Since 1997</div>
    </div>
  </div>

  <div class="tagline">"You open the Harborlane, we'll carry the load"</div>

  <div class="section-rule"><span>We specialize in...</span></div>

  <div class="product fha">
    <div class="product-title">FHA Loans</div>
    <ul class="product-list">
      <li><svg width="14" height="13" viewBox="0 0 14 13"><rect x="1" y="2" width="10" height="10" rx="1.5" fill="none" stroke="#fff" stroke-width="1.6"/><path d="M4 6.5l2.5 2.5L13 1" stroke="#fff" stroke-width="1.8" fill="none"/></svg>Credit Scores as low as 500</li>
      <li><svg width="14" height="13" viewBox="0 0 14 13"><rect x="1" y="2" width="10" height="10" rx="1.5" fill="none" stroke="#fff" stroke-width="1.6"/><path d="M4 6.5l2.5 2.5L13 1" stroke="#fff" stroke-width="1.8" fill="none"/></svg>203K Renovation Loans</li>
    </ul>
  </div>

  <div class="product investor">
    <div class="product-title">Investor Loans</div>
    <ul class="product-list">
      <li><svg width="14" height="13" viewBox="0 0 14 13"><rect x="1" y="2" width="10" height="10" rx="1.5" fill="none" stroke="#fff" stroke-width="1.6"/><path d="M4 6.5l2.5 2.5L13 1" stroke="#fff" stroke-width="1.8" fill="none"/></svg>DSCR, &amp; Fix &amp; Flip</li>
      <li><svg width="14" height="13" viewBox="0 0 14 13"><rect x="1" y="2" width="10" height="10" rx="1.5" fill="none" stroke="#fff" stroke-width="1.6"/><path d="M4 6.5l2.5 2.5L13 1" stroke="#fff" stroke-width="1.8" fill="none"/></svg>Commercial &amp; New Construction</li>
    </ul>
  </div>

  <div class="product conventional">
    <div class="product-title">Conventional Loans</div>
    <ul class="product-list">
      <li><svg width="14" height="13" viewBox="0 0 14 13"><rect x="1" y="2" width="10" height="10" rx="1.5" fill="none" stroke="#fff" stroke-width="1.6"/><path d="M4 6.5l2.5 2.5L13 1" stroke="#fff" stroke-width="1.8" fill="none"/></svg>As little as 1% Down</li>
      <li><svg width="14" height="13" viewBox="0 0 14 13"><rect x="1" y="2" width="10" height="10" rx="1.5" fill="none" stroke="#fff" stroke-width="1.6"/><path d="M4 6.5l2.5 2.5L13 1" stroke="#fff" stroke-width="1.8" fill="none"/></svg>Bank Statement for Self-Employed</li>
    </ul>
  </div>

  <div class="product other">
    <div class="product-title">Other Programs</div>
    <ul class="product-list">
      <li><svg width="14" height="13" viewBox="0 0 14 13"><rect x="1" y="2" width="10" height="10" rx="1.5" fill="none" stroke="#fff" stroke-width="1.6"/><path d="M4 6.5l2.5 2.5L13 1" stroke="#fff" stroke-width="1.8" fill="none"/></svg>HELOCS</li>
      <li><svg width="14" height="13" viewBox="0 0 14 13"><rect x="1" y="2" width="10" height="10" rx="1.5" fill="none" stroke="#fff" stroke-width="1.6"/><path d="M4 6.5l2.5 2.5L13 1" stroke="#fff" stroke-width="1.8" fill="none"/></svg>Reverse Mortgages</li>
    </ul>
  </div>

  <svg class="family-photo" width="927" height="330" viewBox="0 0 927 330" role="img" aria-label="Photo of a happy family celebrating in front of their new house with a home for sale sign">
    <defs>
      <linearGradient id="photoTone" x1="0" y1="0" x2="0" y2="1">
        <stop offset="0" stop-color="var(--photo-top)"/>
        <stop offset="1" stop-color="var(--photo-bottom)"/>
      </linearGradient>
    </defs>
    <circle cx="463" cy="421" r="406" fill="url(#photoTone)"/>
  </svg>

  <div class="contact-card call">
    <div class="icon">
      <svg width="16" height="16" viewBox="0 0 24 24"><path d="M6.6 10.8a15.2 15.2 0 006.6 6.6l2.2-2.2a1 1 0 011-.25 11.4 11.4 0 003.6.57 1 1 0 011 1V20a1 1 0 01-1 1A17 17 0 013 4a1 1 0 011-1h3.5a1 1 0 011 1c0 1.25.2 2.45.57 3.6a1 1 0 01-.25 1z" fill="#062633"/></svg>
    </div>
    <p>Call today for a free<br>consultation</p>
    <p class="big">(800) 914-6027</p>
  </div>

  <div class="contact-card web">
    <div class="icon">
      <svg width="16" height="16" viewBox="0 0 24 24"><circle cx="12" cy="12" r="9" fill="none" stroke="#062633" stroke-width="2.5"/><path d="M7 8l4 1 1 4-3 3-1-3zM14 6l3 2-1 3-2-1z" fill="#062633"/></svg>
    </div>
    <p>Website:<br>www.harborlanehomeloans.com</p>
    <p class="big">NMLS #731860</p>
  </div>
</div>
</body>
</html>
```